Business Card Design (NEW FILES)

ATTENTION: New vector files are available. Please update your design to reflect/use the new (better resolution) logo images.

Seeking a unique and professional business card design for a commercial drone photography/videography business. The layout should feature
the logo (attached) and include the following information:
Owen Tarrick
614-502-7738
www.skylarkreelworks.example
NRD Certified Remote Pilot

Owen Tarrick

```html
<!DOCTYPE html>
<html lang="en">
<head>
<meta charset="utf-8">
<title>Skylark Reelworks – Business Card</title>
<link rel="stylesheet" href="https://fonts.googleapis.com/css2?family=Open+Sans:wght@400;600;700&display=swap">
<style>
  :root {
    --bg: #222222;
    --navy: #1b1c4e;
    --navy-deep: #15163f;
    --navy-light: #2c3a8c;
    --orange: #ea8a47;
    --white: #ffffff;
  }
  * { margin: 0; padding: 0; box-sizing: border-box; }
  html, body {
    width: 1200px; height: 780px; overflow: hidden;
    background: var(--bg);
    font-family: "Open Sans", Arial, sans-serif;
  }
  .stage {
    width: 1200px; height: 780px;
    display: flex; align-items: center; justify-content: center; gap: 40px;
  }
  .card {
    position: relative;
    width: 560px; height: 320px;
    background: var(--navy);
    overflow: hidden;
  }
  /* front */
  .brand {
    position: absolute; left: 30px; top: 30px;
    display: flex; align-items: center; gap: 10px;
    color: var(--white); font-weight: 600; font-size: 24px; letter-spacing: .5px;
  }
  .brand-dot { width: 14px; height: 14px; border-radius: 50%; background: var(--orange); }
  .credentials {
    position: absolute; left: 30px; top: 112px;
    color: var(--white); font-size: 14px; line-height: 1.45;
  }
  .contact {
    position: absolute; left: 30px; top: 172px;
    list-style: none; color: var(--white); font-size: 14px; line-height: 1.55;
  }
  .contact li { display: flex; align-items: center; gap: 8px; }
  .contact svg { width: 12px; height: 12px; flex: none; }
  .hero-art {
    position: absolute; right: 40px; bottom: 0;
    width: 230px; height: 190px;
    background: radial-gradient(ellipse at 65% 70%, rgba(234,138,71,.45), rgba(27,28,78,0) 60%),
                linear-gradient(160deg, #23245c, #181945);
    border-radius: 50% 50% 0 0;
  }
  .person {
    position: absolute; right: 44px; top: 118px; text-align: right;
  }
  .person-name { color: var(--orange); font-weight: 700; font-size: 30px; line-height: 1.1; }
  .person-role { color: var(--white); font-size: 15px; margin-top: 2px; }
  .edge-tab {
    position: absolute; right: 0; top: 170px;
    width: 16px; height: 44px; background: var(--orange);
  }
  /* back */
  .pattern {
    position: absolute; inset: 0;
    background: linear-gradient(135deg, var(--navy-deep) 0%, var(--navy) 45%, var(--navy-light) 100%);
  }
  .back-brand {
    position: absolute; left: 50%; top: 50%; transform: translate(-50%, -50%);
    display: flex; align-items: center; gap: 8px;
    color: var(--white); font-weight: 600; font-size: 18px;
  }
  .back-brand .brand-dot { width: 10px; height: 10px; }
</style>
</head>
<body>
<main class="stage">
  <section class="card card-front">
    <div class="brand"><span class="brand-dot"></span>Skylark Reelworks</div>
    <p class="credentials">NRD Certified Remote Pilot<br>Fully Insured</p>
    <ul class="contact">
      <li>
        <svg viewBox="0 0 12 12"><path d="M3 1 L5 3.5 L4 5 Q5 7 7 8 L8.5 7 L11 9 L9.5 11 Q4 10.5 1 3 Z" fill="var(--orange)"/></svg>
        614-502-7738
      </li>
      <li>
        <svg viewBox="0 0 12 12"><circle cx="6" cy="6" r="5" fill="none" stroke="var(--orange)" stroke-width="1.4"/><path d="M1 6 H11 M6 1 Q3 6 6 11 M6 1 Q9 6 6 11" fill="none" stroke="var(--orange)" stroke-width="1"/></svg>
        www.skylarkreelworks.example
      </li>
      <li>
        <svg viewBox="0 0 12 12"><rect x="1" y="2.5" width="10" height="7" fill="none" stroke="var(--orange)" stroke-width="1.3"/><path d="M1 2.5 L6 7 L11 2.5" fill="none" stroke="var(--orange)" stroke-width="1.3"/></svg>
        info@skylarkreelworks.example
      </li>
    </ul>
    <div class="hero-art" role="img" aria-label="Embossed drone camera illustration with orange propeller accents"></div>
    <div class="person">
      <div class="person-name">Owen Tarrick</div>
      <div class="person-role">Owner</div>
    </div>
    <div class="edge-tab"></div>
  </section>

  <section class="card card-back">
    <div class="pattern" role="img" aria-label="Repeating tonal drone pattern in navy and blue"></div>
    <div class="back-brand"><span class="brand-dot"></span>Skylark Reelworks</div>
  </section>
</main>
</body>
</html>
```